Consulting company business cards

We have a base design, but would be willing to update. We have a new logo/"tag" that needs to be added. Current business card design is attached for reference into our "style."

Industry/Entity Type

Business

Contact Information for Business Card

Should contain name and title, office number, mobile number if appropriate, e-mail, website, physical address, and company logo.

Font styles to use
Other font styles liked:
• See current card design on KorvandBCard

Colors
0455a3
85acd3
aaaaaa

Requirements
Must have
• Our colors are navy blue, gray, and a lighter blue
Nice to have
• Design that I can easily drop in new names/titles as we hire employees.

```html
<!DOCTYPE html>
<html lang="en">
<head>
<meta charset="utf-8">
<title>Torvane Business Card</title>
<link rel="stylesheet" href="https://fonts.googleapis.com/css2?family=Open+Sans:wdth,wght@75..100,300..800&display=swap">
<style>
  :root {
    --navy: #05304f;
    --light-blue: #7aaecb;
    --white: #ffffff;
    --backdrop: #e9ebee;
    --text-navy: #0b2f4d;
  }
  * { margin: 0; padding: 0; box-sizing: border-box; }
  html, body {
    width: 1200px;
    height: 900px;
    overflow: hidden;
    background: var(--backdrop);
  }
  .canvas {
    position: relative;
    width: 1200px;
    height: 900px;
  }
  .business-card {
    position: absolute;
    left: 120px;
    top: 152px;
    width: 960px;
    height: 596px;
    background: var(--white);
    box-shadow: 0 8px 24px rgba(0, 0, 0, 0.18);
    overflow: hidden;
  }
  .business-card svg {
    display: block;
    width: 100%;
    height: 100%;
  }
  .card-text { font-family: "Open Sans", Arial, sans-serif; }
  .brand-name {
    font-weight: 700;
    font-stretch: 75%;
    fill: var(--text-navy);
  }
  .brand-tagline {
    font-size: 13.5px;
    letter-spacing: 1.4px;
    fill: var(--text-navy);
  }
  .person-name { font-size: 20px; font-weight: 600; fill: var(--text-navy); }
  .person-title { font-size: 15.5px; fill: var(--text-navy); }
  .contact-line { font-size: 16px; fill: var(--white); }
  .contact-icon { fill: var(--white); }
  .wave-light { fill: var(--light-blue); }
  .wave-gap { fill: var(--white); }
  .wave-navy { fill: var(--navy); }
  .brand-dot { fill: var(--light-blue); }
</style>
</head>
<body>
<main class="canvas">
  <section class="business-card" aria-label="Torvane business card">
    <svg viewBox="0 0 652 405" xmlns="http://www.w3.org/2000/svg">
      <!-- wave bands -->
      <path class="wave-light" d="M0,226 C70,300 120,334 215,327 C340,318 460,178 560,136 C606,118 636,134 652,172 L652,405 L0,405 Z"/>
      <path class="wave-gap" d="M0,236 C70,309 122,342 217,336 C340,328 462,190 562,152 C606,136 634,150 652,185 L652,405 L0,405 Z"/>
      <path class="wave-navy" d="M0,243 C68,318 124,352 219,346 C342,338 464,202 564,165 C606,150 633,162 652,195 L652,405 L0,405 Z"/>

      <!-- brand -->
      <g class="card-text">
        <text class="brand-name" x="40" y="147" font-size="88" textLength="232" lengthAdjust="spacingAndGlyphs">TORVANE</text>
        <circle class="brand-dot" cx="315" cy="116" r="30"/>
        <text class="brand-tagline" x="41" y="173">A CLOUD CONSULTING COMPANY</text>

        <!-- person -->
        <text class="person-name" x="609" y="64" text-anchor="end">Dana Korvand</text>
        <text class="person-title" x="609" y="89" text-anchor="end">Managing Director</text>

        <!-- contact -->
        <text class="contact-line" x="588" y="249" text-anchor="end">555.014.2910</text>
        <text class="contact-line" x="588" y="272" text-anchor="end">555.014.2971</text>
        <text class="contact-line" x="588" y="296" text-anchor="end">dkorvand@torvanetech.com</text>
        <text class="contact-line" x="588" y="320" text-anchor="end">www.torvanetech.com</text>
        <text class="contact-line" x="609" y="358" text-anchor="end">1180 W 48 th fairview ohio 45011</text>
      </g>

      <!-- icons -->
      <g class="contact-icon">
        <!-- office phone -->
        <path d="M595,240 h14 v3 h-3 l1,3 v4 h-10 v-4 l1,-3 h-3 z"/>
        <!-- mobile -->
        <rect x="598" y="262" width="9" height="13" rx="1.5"/>
        <!-- mail -->
        <path d="M595,287 h14 v10 h-14 z"/>
        <!-- globe -->
        <circle cx="602" cy="315" r="6.5"/>
      </g>
      <path d="M595,287 l7,5 l7,-5" fill="none" stroke="#05304f" stroke-width="1"/>
      <rect x="600" y="265" width="5" height="7" fill="#05304f"/>
      <path d="M599,311 q3,2 2,5 q4,1 5,-3 M598,317 q2,0 3,3" fill="none" stroke="#05304f" stroke-width="1.2"/>
    </svg>
  </section>
</main>
</body>
</html>
```